Need Business Card for our Real Estate Business with Sales Executive's Picture

PANTONE 484 C ( RED)

PANTONE 2766 C ( BLUE

Industry/Entity Type

Real Estate

Contact Information for Business Card

Name, Mobile, email, & picture of Person
Agency Phone, address, Web address

Requirements
Must have
• Our Logo Colours, Agent Picture,

```html
<!DOCTYPE html>
<html lang="en">
<head>
<meta charset="utf-8">
<title>Meridian Real Estate – Business Card</title>
<link rel="stylesheet" href="https://fonts.googleapis.com/css2?family=Roboto:wght@400;500&family=Roboto+Condensed:wght@500;700&display=swap">
<style>
  :root {
    --navy: #0a1538;
    --red: #7a1a1f;
    --paper: #f3f3f3;
    --ink: #4a4a4a;
    --backdrop: #e4e2df;
    --photo-top: #c9cdd6;
    --photo-bottom: #1f3a86;
  }
  * { margin: 0; padding: 0; box-sizing: border-box; }
  html, body { width: 1200px; height: 960px; overflow: hidden; }
  body {
    background: var(--backdrop);
    font-family: "Roboto", Arial, sans-serif;
    position: relative;
  }
  .card {
    position: absolute;
    width: 600px;
    height: 343px;
    box-shadow: 0 2px 6px rgba(0,0,0,0.25);
  }
  .card--front { left: 314px; top: 113px; background: var(--paper); }
  .card--back { left: 311px; top: 472px; background: var(--navy); }

  .brand {
    position: absolute;
    font-family: "Roboto", Arial, sans-serif;
    font-weight: 500;
    text-transform: uppercase;
    display: flex;
    align-items: center;
    white-space: nowrap;
  }
  .card--front .brand {
    left: 32px; top: 116px;
    font-size: 19px; letter-spacing: 1px; gap: 8px;
    color: var(--navy);
  }
  .card--front .brand__mark { width: 12px; height: 12px; background: var(--navy); }
  .card--back .brand {
    left: 0; right: 0; top: 196px; justify-content: center;
    font-size: 28px; letter-spacing: 2px; gap: 10px;
    color: #fff;
  }
  .card--back .brand__mark { width: 14px; height: 14px; background: #fff; }

  .person { position: absolute; left: 32px; top: 184px; }
  .person__name {
    font-family: "Roboto Condensed", Arial, sans-serif;
    font-weight: 700;
    font-size: 21px;
    color: var(--navy);
    line-height: 26px;
  }
  .person__role {
    font-family: "Roboto Condensed", Arial, sans-serif;
    font-weight: 500;
    font-size: 15.5px;
    color: var(--red);
    line-height: 20px;
    margin-top: 2px;
  }
  .address {
    position: absolute; left: 32px; top: 239px;
    font-size: 14.5px; line-height: 18px; color: var(--ink);
  }
  .contacts {
    position: absolute; left: 32px; top: 283px;
    font-size: 14.5px; color: var(--ink);
  }
  .contacts__row { display: flex; align-items: center; height: 20px; gap: 6px; }
  .contacts__item { display: flex; align-items: center; gap: 6px; }
  .icon { width: 13px; height: 13px; fill: var(--navy); flex: none; }

  .portrait {
    position: absolute; right: 14px; bottom: 0;
    width: 232px; height: 318px;
    background: linear-gradient(180deg, var(--photo-top) 0%, var(--photo-bottom) 60%);
    border-radius: 110px 110px 0 0;
  }

  .card--back .web {
    position: absolute; left: 0; right: 0; top: 296px;
    text-align: center; color: #fff;
    font-size: 14px; letter-spacing: 4px;
  }
</style>
</head>
<body>
  <section class="card card--front">
    <div class="brand"><span class="brand__mark"></span>Meridian Real Estate</div>

    <div class="person">
      <div class="person__name">DANIEL REYES</div>
      <div class="person__role">CEO/FOUNDER</div>
    </div>

    <div class="address">4120 Willow Creek Road<br>Juneau, Alaska 34512</div>

    <div class="contacts">
      <div class="contacts__row">
        <span class="contacts__item">
          <svg class="icon" viewBox="0 0 24 24"><path d="M6.6 10.8a15.1 15.1 0 0 0 6.6 6.6l2.2-2.2c.3-.3.7-.4 1-.2 1.1.4 2.3.6 3.6.6.6 0 1 .4 1 1V20c0 .6-.4 1-1 1A17 17 0 0 1 3 4c0-.6.4-1 1-1h3.5c.6 0 1 .4 1 1 0 1.3.2 2.5.6 3.6.1.3 0 .7-.2 1z"/></svg>
          555 210 4471
        </span>
        <span class="contacts__item">
          <svg class="icon" viewBox="0 0 24 24"><path d="M7 1h10a2 2 0 0 1 2 2v18a2 2 0 0 1-2 2H7a2 2 0 0 1-2-2V3a2 2 0 0 1 2-2zm0 3v14h10V4zm5 15.5a1.2 1.2 0 1 0 0 2.4 1.2 1.2 0 0 0 0-2.4z"/></svg>
          555 318 0926
        </span>
      </div>
      <div class="contacts__row">
        <span class="contacts__item">
          <svg class="icon" viewBox="0 0 24 24"><path d="M2 5h20v14H2zm2 2v.5l8 5 8-5V7zm0 2.8V17h16V9.8l-8 5z"/></svg>
          dan@meridian.com
        </span>
        <span class="contacts__item">
          <svg class="icon" viewBox="0 0 24 24"><path d="M12 2a10 10 0 1 0 0 20 10 10 0 0 0 0-20zm-1 17.9A8 8 0 0 1 4.2 10L9 14.8V16a2 2 0 0 0 2 2zm6.9-2.5A2 2 0 0 0 16 16h-1v-3a1 1 0 0 0-1-1H8v-2h2a1 1 0 0 0 1-1V7h2a2 2 0 0 0 2-2v-.4a8 8 0 0 1 2.9 12.8z"/></svg>
          www.meridian.com
        </span>
      </div>
    </div>

    <div class="portrait" role="img" aria-label="Portrait photo of the agent in a navy suit and striped tie"></div>
  </section>

  <section class="card card--back">
    <div class="brand"><span class="brand__mark"></span>Meridian Real Estate</div>
    <div class="web">www.meridian.com</div>
  </section>
</body>
</html>
```